Agrarhandel benötigt Homepage
Zielgruppe
Wir sind ein Agrarhandel mit einem Warenumschlagslager im Sinne eines klassischen Einzelhandels und vertreiben Produkte an Landwirte.
Wir vertreiben folgende Hauptproduktgruppen:
Einzelfuttermittel
wie z.B. Sojaexktraktionsschrot. Die einzelnen Produkte könnten z.B. wie die Futtermittel auf folgender Seite dargestellt werden (https://www.kornprobe-beispiel.eu/de/produkt/trelomixan)
Mischfuttermittel
Hier bieten wir unseren Kunden an, individuelles Mischfutter auf Basis unserer Einzelfuttermittel herzustellen.
Weitere Details und weitere Produktbereiche habe ich in einer Powerpoint-Übersicht dargestellt.
Neben diesen Produkten wollen wir uns als Familienunternehmen selbst vorstellen. Zudem betreiben wir in unserer Familie zusätzlich einen Milchviehbetrieb den wir ebenfalls hervorheben möchten, da wir unseren Kunden gegenüber einerseits als Zulieferer aber auch als Kollege auftreten wollen.
Einzelfuttermittel: Hier können wir durch unsere Unabhängigkeit punkten, da wir nicht abhängig von bestimmten Lieferanten sind und dementsprechend unabhängig beraten können. Wir untersuchen im Vergleich zu unseren Wettbewerben die Qualität der Futtermittel bis ins Detail und können daher eine Transparenz bieten, die Konkurrenten in der Regel nicht bieten können. Unser Warenumschlagsplatz mit moderner Technik ermöglicht es uns äußerst kosteneffizient die Waren umschlagen und ausliefern zu können.
Mischfuttermittel: Auf Basis der vorhandenen Einzelfuttermittel stellen wir je nach Kundenwunsch individuelle Mischfutter her. Wir arbeiten mit offenen Deklarationen, sodass unsere Kunden jederzeit nachvollziehen können, ob auch die Einzelfuttermittel verwendet wurden, die sie bestellt haben und keine billigen Ersatzprodukte verwendet wurden.
Zudem sind wir BT und HUPA zertifiziert. Die aktuellen für unser Unternehmen ausgestellten Zertifikate müssen für unsere Kunden als Download zur Verfügung stehen. Statt dem HUPA-Logo bitte das ..
Aufgabenstellung
Wir möchten gerne ein zeitgemäße Homepage, jedoch muss auch berücksichtigt werden, dass unsere Kunden eher konservativ denken.

```html
<!DOCTYPE html>
<html lang="de">
<head>
<meta charset="utf-8">
<title>Talgrund Agrar – Familienbetrieb mit Tradition</title>
<link rel="stylesheet" href="https://fonts.googleapis.com/css2?family=Open+Sans:ital,wght@0,400;0,600;0,700;1,400&family=Ubuntu:wght@500&display=swap">
<style>
:root{
  --green:#17694d;
  --green-dark:#0e4a37;
  --green-mid:#136048;
  --gold:#f4b41a;
  --text:#2b2b2b;
  --ink:#1d1d1d;
  --white:#ffffff;
  --black:#000000;
}
*{margin:0;padding:0;box-sizing:border-box}
html,body{width:1200px;height:2531px;overflow:hidden;background:var(--white)}
body{position:relative;font-family:"Open Sans",Arial,sans-serif;color:var(--text)}
.topbar{position:absolute;left:0;top:0;width:1200px;height:38px;background:linear-gradient(90deg,var(--green-dark),var(--green));display:flex;justify-content:flex-end;align-items:center;padding-right:100px;color:var(--white);font-size:13px;font-weight:600;gap:12px}
.icon{width:20px;height:20px;border-radius:50%;background:var(--gold);display:inline-flex;align-items:center;justify-content:center;flex:none}
.topbar .icon{margin-left:4px}
.nav{position:absolute;top:38px;left:0;width:1200px;height:100px;background:var(--white);font-size:13px;font-weight:600;color:var(--ink)}
.nav a{position:absolute;top:50px;color:var(--ink);text-decoration:none}
.burger{position:absolute;left:1072px;top:50px;width:28px}
.burger span{display:block;height:3px;background:#5a4a3a;margin-bottom:3px}
.brand-disc{position:absolute;left:503px;top:18px;width:194px;height:194px;border-radius:50%;background:var(--white);z-index:3;display:flex;align-items:center;justify-content:center;color:var(--green);font-family:"Open Sans",sans-serif;font-weight:700;font-size:17px;text-align:center;line-height:1.2}
.hero{position:absolute;left:0;top:138px;width:1200px;height:550px;background:linear-gradient(180deg,#a9ab9c 0%,#7c8a6a 40%,#5b6a40 70%,#4d5b30 100%)}
.dots{position:absolute;left:0;top:643px;width:1200px;display:flex;justify-content:center;gap:7px;z-index:2}
.dots i{width:11px;height:11px;border-radius:50%;background:rgba(255,255,255,.6)}
.dots i:first-child{background:var(--white)}
.section-title{position:absolute;left:0;width:1200px;text-align:center;font-family:"Ubuntu",sans-serif;font-weight:500;font-size:43px;line-height:57px;color:var(--green)}
.columns{position:absolute;left:100px;width:1000px;column-count:2;column-gap:24px;font-size:13.6px;line-height:18.8px;text-align:justify;hyphens:auto}
.columns p{margin-bottom:18.8px}
.columns b{font-weight:700;color:var(--ink)}
.photo-band{position:absolute;left:0;top:1161px;width:1200px;height:439px;background:linear-gradient(180deg,#6f7275 0%,#9a9a94 35%,#5e5a52 70%,#b9a888 100%)}
.footer{position:absolute;left:0;top:2118px;width:1200px;height:342px;display:flex;color:var(--white)}
.f-brand{width:494px;background:var(--green-dark);text-align:center;padding-top:150px}
.f-brand .name{font-weight:700;font-size:19px;letter-spacing:.3px}
.f-brand .addr{margin-top:20px;font-size:13px;line-height:18px}
.contacts{margin:26px 0 0 110px;display:grid;grid-template-columns:142px 200px;row-gap:10px;text-align:left;font-size:13px}
.contacts div{display:flex;align-items:center;gap:10px}
.f-info{width:211px;background:var(--green-mid);border-left:1px solid rgba(255,255,255,.6);border-right:1px solid rgba(255,255,255,.6);text-align:center;padding-top:52px}
.f-head{font-weight:700;font-size:14px;letter-spacing:.4px}
.f-info ul{list-style:none;margin-top:66px;font-size:13px;line-height:18px}
.f-about{flex:1;background:var(--green);text-align:center;padding-top:52px}
.f-about p{margin:50px auto 0;width:290px;font-style:italic;font-size:11.5px;line-height:18.5px}
.copyright{position:absolute;left:0;top:2460px;width:1200px;height:71px;background:var(--black);color:var(--white);font-size:13px;text-align:center;padding-top:12px}
</style>
</head>
<body>
<div class="topbar">Jetzt telefonisch beraten lassen
  <span class="icon"><svg width="11" height="11" viewBox="0 0 24 24"><path fill="#fff" d="M6.6 10.8a15 15 0 0 0 6.6 6.6l2.2-2.2c.3-.3.7-.4 1-.2 1.1.4 2.3.6 3.6.6.6 0 1 .4 1 1V20c0 .6-.4 1-1 1A17 17 0 0 1 3 4c0-.6.4-1 1-1h3.5c.6 0 1 .4 1 1 0 1.3.2 2.5.6 3.6.1.3 0 .7-.2 1z"/></svg></span>
  09876 543210</div>
<nav class="nav">
  <a style="left:100px">EINZELFUTTERMITTEL</a>
  <a style="left:284px">MISCHFUTTERMITTEL</a>
  <a style="left:725px">ÜBER UNS</a>
  <a style="left:831px">UNSER BETRIEB</a>
  <a style="left:970px">KONTAKT</a>
  <div class="burger"><span></span><span></span><span></span></div>
</nav>
<div class="brand-disc">Talgrund<br>Agrar</div>
<div class="hero" role="img" aria-label="Landwirt auf einer Weide vor einer Herde Milchkühe"></div>
<div class="dots"><i></i><i></i><i></i></div>

<h1 class="section-title" style="top:751px">FAMILIENBETRIEB MIT<br>TRADITION</h1>
<div class="columns" style="top:890px">
<p>Wir, die Familie Berger aus Lindach bei Mooshof, führen einen hochmodernen Milchviehbetrieb und betreiben einen eigenen (Futtermittel-) Agrarhandel. Unser Unternehmen zeichnet sich durch <b>Unabhängigkeit</b> von Beteiligungsstrukturen und vertraglichen Abhängigkeiten im Hintergrund aus. Durch eine direkte Anbindung an regionale Futtermittelhersteller und den Einsatz unseres eigenen Lkw können wir effizient und flexibel Waren an unsere Kunden ausliefern.</p>
<p>Im Unterschied zu vielen Mitbewerbern besitzen wir ein <b>eigenes Lagerhaus,</b> was es uns ermöglicht, <b>europaweit</b> Futtermittel von Herstellern und Großhändlern zu beziehen, wie beispielsweise aus Italien, den Niederlanden oder der Slowakei. Unser Standort dient als zentraler Warenumschlagspunkt, wodurch wir unseren Kunden die Möglichkeit bieten, von den <b>Preis- und Qualitätsunterschieden</b> der Hersteller in ganz Europa zu profitieren. Viele unserer Wettbewerber sind jedoch an einen Hersteller oder einen Hafen gebunden und können oft nur die dort verfügbaren Produkte anbieten. Eine einseitige Beratung ist oft die Konsequenz.</p>
<p><b>Unser Ziel</b> ist es, die <b>attraktivsten Einzelfuttermittel</b> von verschiedenen Herstellern anzubieten und bei Bedarf <b>kundenindividuelle Mischfutter</b> in <b>unserer eigenen Mischanlage</b> herzustellen. Diese Vielseitigkeit ist es, die unsere Kunden an unserem Betrieb schätzen.</p>
</div>

<div class="photo-band" role="img" aria-label="Familie geht durch einen Milchviehstall zwischen fressenden Kühen"></div>

<h2 class="section-title" style="top:1664px">UNSER<br>QUALITÄTSVERSPRECHEN</h2>
<div class="columns" style="top:1824px">
<p>Für unsere Kunden setzen wir auf eine <b>konsequente Qualitätspolitik</b>, die im Vergleich zu einigen Wettbewerbern, auf die teuren und oft aufdringlichen Außendienstler verzichtet. Stattdessen setten wir auf <b>regelmäßige Untersuchungen</b> unserer Futtermittel. So lassen wir standardmäßig die vielfach teure Rohproteinfraktionierung durchführen, um auch den UDP-8-Gehalt zu erhalten! Die <b>Ergebnisse</b> stellen wir unseren Kunden, deren Beratern und dem <b>Landwirtschaftsamt Eichenau</b> selbstverständlich <b>zur Bewertung zur Verfügung</b>.</p>
<p>Die Durchschnittswerte der Untersuchungsergebnisse bilden dabei die Basis für unsere Futtermitteldeklaration. Dies ermöglicht es uns, unseren Kunden eine <b>belastbarere</b> Grundlage für die betriebsindividuelle <b>Rationsberechnung</b> an die Hand zu geben. Damit wollen wir den Schwankungen gerecht werden, welche sich aus der Eigenschaft als Naturprodukt und durch die Messtoleranzen ergeben!</p>
<p>Als <b>BT-zertifiziertes Unternehmen</b> unterziehen wir unsere Futtermittel regelmäßigen Untersuchungen auf Schadstoffe. Selbstverständlich ziehen wir Proben bei Bedarf gemeinsam mit unseren Kunden aus unseren Lagerbeständen, um höchste Transparenz und Vertrauen zu gewährleisten. Zögern Sie nicht, uns darauf anzusprechen!</p>
</div>

<footer class="footer">
  <div class="f-brand">
    <div class="name">TALGRUND AGRAR</div>
    <div class="addr">Feldweg 12<br>91234 Mooshof</div>
    <div class="contacts">
      <div><span class="icon"></span>09876 54 32 10</div>
      <div><span class="icon"></span>info@talgrund-agrar.de</div>
      <div><span class="icon"></span>0170 123 45 67</div>
      <div><span class="icon"></span>www.talgrund-agrar.de</div>
    </div>
  </div>
  <div class="f-info">
    <div class="f-head">INFORMATIONEN</div>
    <ul><li>AGB</li><li>Datenschutz</li><li>Kontakt</li><li>Impressum</li><li>Sitemap</li></ul>
  </div>
  <div class="f-about">
    <div class="f-head">ÜBER UNS</div>
    <p>Wir von Talgrund Agrar sind ein Familienunternehmen für Einzel- und Mischfutter. Unsere jahrelange Erfahrung durch unseren eigenen Milchviehbetrieb zeigt uns, wie wichtig hochwertige Nahrung für das Tierwohlbefinden ist. Dieses Wissen wollen wir an unsere Kunden weitergeben.</p>
  </div>
</footer>
<div class="copyright">©2023 Talgrund Agrar</div>
</body>
</html>
```